Professional & attention grabbing.

A business card design, front and back. I already have a logo I will attach, but I am open to something new as well.
Things to include:
Name:
Title:
Phone:
Email:
Wanting something that is professional but attention grabbing.
Also we do a lot of work using drones on natural gas pipelines (leading the future)if you want to include any of that. I'm open to ideas.
Target Market(s)
Natural gas transmission industry / greenhouse gas mitigation industry
Industry/Entity Type
Business
Colors
Designer to choose colors to be used in the design.
Look and feel
Each slider illustrates characteristics of the customer's brand and the style your logo design should communicate.

```html
<!DOCTYPE html>
<html lang="en">
<head>
<meta charset="utf-8">
<title>Veyra Inspections – Business Card</title>
<link href="https://fonts.googleapis.com/css2?family=Roboto:wght@400;500;700&display=swap" rel="stylesheet">
<style>
  :root {
    --page-bg: #d8d4cf;
    --card-bg: #f4f3f1;
    --ink-dark: #2f2c2b;
    --ink-body: #3a3737;
    --accent-red: #a61d22;
  }
  html, body {
    margin: 0;
    padding: 0;
    width: 1200px;
    height: 1010px;
    overflow: hidden;
    background: var(--page-bg);
    font-family: "Roboto", Arial, sans-serif;
  }
  .business-card {
    position: absolute;
    left: 100px;
    top: 215px;
    width: 1000px;
    height: 580px;
    background: var(--card-bg);
    box-shadow: 0 10px 30px rgba(0,0,0,0.12);
  }
  .name-bar {
    position: absolute;
    left: 0;
    top: 89px;
    width: 29px;
    height: 110px;
    background: var(--ink-dark);
  }
  .holder-name {
    position: absolute;
    left: 51px;
    top: 106px;
    margin: 0;
    font-size: 31px;
    font-weight: 700;
    letter-spacing: 1.5px;
    color: var(--accent-red);
  }
  .holder-title {
    position: absolute;
    left: 51px;
    top: 150px;
    margin: 0;
    font-size: 20px;
    font-weight: 400;
    color: var(--ink-body);
  }
  .brand {
    position: absolute;
    right: 67px;
    top: 110px;
    display: flex;
    align-items: center;
    gap: 16px;
  }
  .brand-square {
    width: 44px;
    height: 44px;
    background: var(--accent-red);
  }
  .brand-name {
    margin: 0;
    font-size: 40px;
    font-weight: 700;
    color: var(--ink-dark);
    letter-spacing: 0.5px;
  }
  .contact-list {
    position: absolute;
    left: 51px;
    top: 434px;
    margin: 0;
    padding: 0;
    list-style: none;
  }
  .contact-item {
    display: flex;
    align-items: center;
    height: 33px;
    font-size: 21px;
    color: var(--ink-body);
  }
  .contact-icon {
    width: 22px;
    height: 22px;
    margin-right: 20px;
    fill: var(--accent-red);
  }
</style>
</head>
<body>
  <section class="business-card">
    <div class="name-bar"></div>
    <h1 class="holder-name">DANIEL MARSH</h1>
    <p class="holder-title">Managing Director</p>

    <div class="brand">
      <div class="brand-square"></div>
      <p class="brand-name">Veyra Inspections</p>
    </div>

    <ul class="contact-list">
      <li class="contact-item">
        <svg class="contact-icon" viewBox="0 0 24 24" aria-hidden="true">
          <path d="M3 9c0-3 4-5 9-5s9 2 9 5v2h-5V9c-1-1-7-1-8 0v2H3z"/>
          <path d="M6 13h12l2 7H4z"/>
        </svg>
        1300 478 910
      </li>
      <li class="contact-item">
        <svg class="contact-icon" viewBox="0 0 24 24" aria-hidden="true">
          <path d="M12 2a10 10 0 1 0 0 20a10 10 0 0 0 0-20zm0 2c1.2 0 2.5 2.2 3 6H9c.5-3.8 1.8-6 3-6zM4.3 10h2.7c.1-2 .5-3.7 1.1-5A8 8 0 0 0 4.3 10zm0 4a8 8 0 0 0 3.8 5c-.6-1.3-1-3-1.1-5zm4.7 0h6c-.5 3.8-1.8 6-3 6s-2.5-2.2-3-6zm8 0c-.1 2-.5 3.7-1.1 5a8 8 0 0 0 3.8-5zm2.7-4a8 8 0 0 0-3.8-5c.6 1.3 1 3 1.1 5z"/>
        </svg>
        www.veyrainspect.com
      </li>
      <li class="contact-item">
        <svg class="contact-icon" viewBox="0 0 24 24" aria-hidden="true">
          <path d="M2 5h20v2l-10 6L2 7z"/>
          <path d="M2 9l10 6 10-6v10H2z"/>
        </svg>
        daniel.marsh@veyrainspect.com
      </li>
    </ul>
  </section>
</body>
</html>
```